Small Business Directory Site Requires a Professional Responsive Web Design

Small Business Directory and Coupon Site - we require a complete website design for a brand new responsive & mobile friendly website. We already have a coder who will professional code our website in Magento.

All PSD pages need to be professionally designed then uploaded into a sharedrive (i.e. like filecrate). Additionally, as I cannot pre-empt everything, please note that we may require a little more assistance once the files have been transferred (for example, in www.brightlane-listings.example if you hover your mouse on the search box you will see a pop up box. We want one of these too and I think that means there may be extra design work here)

We have some draft page sketches have been created (there are some minor changes we want to the sketches provided though); however, we require an excellent designer to add the creative touches to it to make it look professionally created. All artwork/font must be legal.

-------------------------
We like the look of the www.brightlane-listings.example and www. marlowfolio.example

For the headers, please consider a font similar to RNS camellia. We likes this style, but it is too thin for the headers...so we need a variation like this one. For the copy/general text font, something basic that marries well with the headers.

---------------------

Please be sure to also read the brief we wrote for the coder as this will help with better understanding our design requirements.

In total I believe we have about 50 pages. This includes all the little pages and most of the pop up boxes (but not the little help key boxes). For example, pages include...

1. Login (this is where customers log in and can edit, manage their profiles. This means that there are backend membership pages)
2. Mini Services (same look and feel as the business coupons)
3. Resource Centre
4. Join (this is where customers learn about the packages available to submit a directory listing, if they ‘buy’ a package (i.e. free, $25 or $150 package) then they can create their own directory listing)
5. Search the directory (customer can view all the categories and also search the directory)
6. Create a directory listing (this is where customers learn about the packages available to submit a directory listing, if they ‘buy’ a package (i.e. free, $25 or $150 package) then they can create their own directory listing)
7. Quote finder (also know as Get a Quote)
8. Coupons (customer go to the business coupon page and can view all current coupons/submit a coupon)
9. Submit a coupon (form)
10.Advertise with us (form)
11. Join the forum
12.Submit an article or video (form)
13. Affiliates (listing of affiliates we currently have)
14. Become an affiliate (form)
15. Case studies (customer can view the case studies we have in the resource centre)
16. Help Guides (customer can view the help guides we have in the resource centre)
17. About Us
18 .Contact Us (form)
19. Terms & Condition
20. Privacy Policy
21. Supporting City Councils
22. Site Map
23. Forgot password / login details
24. Homepage
25. If we hover over a few areas (i.e. search box, location field) it pops up with more information.
etc etc etc. . . there are more pages.

Please see our filecrate link for the draft mock up pages that I have created so far.

https://www.cloudtrunk.example/sh/qk72pmw4rtz8nd/KLMvbTq2fWndxPzs8Yh4ecRQu

We are in a rush! We'd like to get the majority of the artwork completed by the end of the month. Minor fixes/tweaks can occur thereafter.

Target Market(s)

Small Businesses (employees 0 - 50) located throughout Australia

Industry/Entity Type

Business

Font styles to use
Sans Serif

Requirements
Must have
• Professional. Artwork must be legal (cannot be cut and paste or taken off other websites, must be legally purchased and used).Must look contemporary, fresh, modern.

Absolutely must be a responsive site!
Nice to have
• original work, original photos, original art.

like modern, fresh photos that demonstrate innovation, growth, small business, Australian scenery, stability, goals/passion.
Should not have
• cut and paste graphics, illegal graphics, not purchased graphics.

```html
<!DOCTYPE html>
<html lang="en">
<head>
<meta charset="utf-8">
<title>TradeNest Link — Small Business Directory</title>
<link href="https://fonts.googleapis.com/css2?family=Open+Sans:wght@300;400;600;700&display=swap" rel="stylesheet">
<style>
  :root {
    --orange: #f26a10;
    --orange-text: #e8661a;
    --ink: #1f1f1f;
    --body-grey: #555555;
    --white: #ffffff;
    --band-blue: #7db4e6;
    --footer-bg: #151515;
    --footer-bar: #111111;
    --footer-link: #d8d8d8;
    --hero-top: #7a3a4e;
    --hero-mid: #d9801e;
    --hero-low: #8a3f2c;
    --font: "Open Sans", sans-serif;
  }
  * { box-sizing: border-box; margin: 0; padding: 0; }
  html, body { width: 1019px; height: 1200px; overflow: hidden; background: var(--white); }
  body { position: relative; font-family: var(--font); color: var(--ink); }

  /* Header */
  .site-header { position: absolute; left: 0; top: 0; width: 1019px; height: 97px; background: var(--white); }
  .brand { position: absolute; left: 106px; top: 30px; display: flex; align-items: center; gap: 10px; }
  .brand-mark { width: 34px; height: 34px; background: var(--orange); }
  .brand-name { font-size: 30px; font-weight: 600; color: var(--ink); letter-spacing: -0.5px; }
  .main-nav { position: absolute; top: 50px; left: 537px; display: flex; gap: 21px; font-size: 11px; font-weight: 400; color: var(--ink); }

  /* Hero */
  .hero { position: absolute; left: 0; top: 97px; width: 1019px; height: 395px; }
  .hero-scene {
    position: absolute; inset: 0;
    background:
      radial-gradient(circle at 50% 40%, #f2a62a 0, #e58a1d 14%, transparent 32%),
      linear-gradient(180deg, var(--hero-top) 0%, #c4622a 30%, var(--hero-mid) 55%, var(--hero-low) 80%, #6e2f3a 100%);
  }
  .hero-title { position: absolute; left: 101px; top: 132px; font-size: 24px; font-weight: 400; color: var(--white); letter-spacing: 0.2px; }
  .hero-sub { position: absolute; left: 102px; top: 172px; font-size: 11px; color: var(--white); }
  .search-bar { position: absolute; left: 102px; top: 209px; width: 496px; height: 46px; background: var(--orange); }
  .search-field { position: absolute; top: 6px; height: 34px; background: var(--white); border: 1px solid #e4e4e4; }
  .search-field.what { left: 7px; width: 237px; }
  .search-field.where { left: 286px; width: 146px; }
  .search-near { position: absolute; left: 252px; top: 16px; font-size: 11px; color: #5a2a10; }
  .search-btn { position: absolute; left: 444px; top: 8px; width: 30px; height: 30px; border-radius: 50%; background: #1c1c1c; }

  .offer-card { position: absolute; left: 645px; top: 85px; width: 260px; height: 290px; background: var(--white); text-align: center; }
  .offer-title { margin-top: 18px; font-size: 22px; line-height: 29px; font-weight: 400; color: var(--orange-text); }
  .offer-count { margin-top: 18px; font-size: 14px; color: var(--ink); }
  .price-band { position: absolute; left: 632px; top: 208px; width: 286px; height: 48px; background: var(--band-blue); color: var(--white); text-align: center; line-height: 48px; font-size: 21px; font-weight: 400; box-shadow: 0 3px 6px rgba(0,0,0,0.15); }
  .price-band small { font-size: 13px; }
  .band-arrow { position: absolute; top: 224px; width: 20px; height: 21px; background: #f1f1f1; border-radius: 2px; }
  .band-arrow.prev { left: 622px; }
  .band-arrow.next { left: 909px; }
  .band-arrow svg { display: block; margin: 5px auto 0; }
  .offer-desc { position: absolute; left: 645px; top: 276px; width: 260px; text-align: center; font-size: 12.5px; line-height: 19px; color: var(--ink); }
  .checkout-btn { position: absolute; left: 722px; top: 336px; width: 108px; height: 21px; border-radius: 11px; background: var(--orange); text-align: center; font-size: 10px; font-weight: 600; line-height: 21px; color: var(--white); }

  /* Community */
  .section-title { position: absolute; left: 0; top: 528px; width: 1019px; text-align: center; font-size: 20px; font-weight: 400; color: var(--orange-text); }
  .feature { position: absolute; top: 579px; width: 248px; text-align: center; }
  .feature h3 { font-size: 14.5px; font-weight: 400; color: var(--ink); height: 35px; }
  .feature-media { position: relative; width: 248px; height: 158px; }
  .feature p { margin: 14px auto 0; width: 232px; font-size: 10.6px; line-height: 19.2px; color: var(--body-grey); font-weight: 400; }
  .media-desk { background: linear-gradient(135deg, #eef1f6 0%, #cfd6e2 55%, #9aa6b8 100%); }
  .media-video { background: linear-gradient(135deg, #6b5a4a 0%, #a88a68 45%, #4a3a30 100%); }
  .play-icon { position: absolute; left: 96px; top: 51px; }
  .media-partner { background: var(--white); border: 1px solid #d6d6d6; }
  .partner-name { position: absolute; left: 0; top: 52px; width: 100%; display: flex; justify-content: center; align-items: center; gap: 8px; font-size: 26px; font-weight: 700; color: #17305a; }
  .partner-dot { width: 22px; height: 22px; border-radius: 50%; background: #1b82c9; }
  .slide-arrow { position: absolute; bottom: 4px; width: 18px; height: 18px; background: #f1f1f1; }
  .slide-arrow.prev { left: 3px; }
  .slide-arrow.next { right: 3px; }
  .slide-arrow svg { display: block; margin: 4px auto 0; }

  /* Footer */
  .site-footer { position: absolute; left: 0; top: 943px; width: 1019px; height: 217px; background: var(--footer-bg); }
  .footer-col { position: absolute; top: 26px; }
  .footer-col h4 { font-size: 12.5px; font-weight: 400; color: var(--orange-text); margin-bottom: 20px; }
  .footer-col li { list-style: none; font-size: 11px; line-height: 19.2px; color: var(--footer-link); }
  .social-icon { position: absolute; left: 842px; width: 24px; height: 24px; border-radius: 4px; }
  .social-a { top: 67px; background: #2aa3e8; }
  .social-b { top: 101px; background: #d8312a; }
  .social-c { top: 137px; background: #3b5b9a; }
  .social-d { top: 173px; background: #1a78b8; }
  .footer-bar { position: absolute; left: 0; top: 1160px; width: 1019px; height: 40px; background: var(--footer-bar); border-top: 1px solid #222; text-align: center; font-size: 11px; line-height: 38px; color: #bdbdbd; }
</style>
</head>
<body>

<header class="site-header">
  <div class="brand">
    <span class="brand-mark"></span>
    <span class="brand-name">TradeNest Link</span>
  </div>
  <nav class="main-nav">
    <span>LOGIN</span><span>JOIN</span><span>FEATURE&nbsp; YOUR OFFER</span><span>GET A QUOTE</span><span>ADVERTISE</span>
  </nav>
</header>

<section class="hero">
  <div class="hero-scene" role="img" aria-label="Sunset over a tropical beach with palm tree silhouettes"></div>
  <h1 class="hero-title">IT'S A BRAND NEW DAY</h1>
  <div class="hero-sub">DO MORE OF WHAT YOU LOVE</div>
  <div class="search-bar">
    <div class="search-field what"></div>
    <span class="search-near">NEAR</span>
    <div class="search-field where"></div>
    <div class="search-btn">
      <svg width="30" height="30" viewBox="0 0 30 30"><circle cx="16" cy="13" r="6" fill="none" stroke="#f26a10" stroke-width="2"/><line x1="11.5" y1="17.5" x2="8" y2="21" stroke="#f26a10" stroke-width="2.4" stroke-linecap="round"/></svg>
    </div>
  </div>

  <div class="offer-card">
    <div class="offer-title">CREATE A DIRECTORY<br>LISTING TODAY</div>
    <div class="offer-count">3 CATEGORY LISTING</div>
  </div>
  <div class="price-band">A $25/ <small>YEAR</small></div>
  <div class="band-arrow prev"><svg width="8" height="11" viewBox="0 0 8 11"><path d="M6 1 L2 5.5 L6 10" fill="none" stroke="#222" stroke-width="2"/></svg></div>
  <div class="band-arrow next"><svg width="8" height="11" viewBox="0 0 8 11"><path d="M2 1 L6 5.5 L2 10" fill="none" stroke="#222" stroke-width="2"/></svg></div>
  <div class="offer-desc">Promote Your Special Offers Business<br>Profile &amp; Logo Website &amp; Email Link</div>
  <div class="checkout-btn">Check out with Lumora</div>
</section>

<h2 class="section-title">GET REAL SUPPORT FROM OUR COMMUNITY</h2>

<article class="feature" style="left:102px">
  <h3>How Did You Sort Your Business?</h3>
  <div class="feature-media media-desk" role="img" aria-label="Hand typing on a keyboard beside paperwork and a pen"></div>
  <p>Learn from Mara Ellison, a real small business owner. How she started her business and what are the most valuable resources for her right now.</p>
</article>

<article class="feature" style="left:388px">
  <h3>Why Go with TradeNest Link?</h3>
  <div class="feature-media media-video" role="img" aria-label="Video thumbnail of a business owner checking stock in a warehouse">
    <svg class="play-icon" width="56" height="56" viewBox="0 0 56 56"><circle cx="28" cy="28" r="25" fill="none" stroke="#fff" stroke-width="3.5"/><path d="M22 16 L40 28 L22 40 Z" fill="#fff"/></svg>
  </div>
  <p>What small business owner can’t relate to the ongoing task of attracting new customers? Struggling with cash flow? Or how about not having enough time in the day?<br>It’s obvious that small businesses suffer from a lack of support &amp; that’s where we come in.</p>
</article>

<article class="feature" style="left:677px">
  <h3>Become an Affiliate</h3>
  <div class="feature-media media-partner">
    <div class="partner-name"><span class="partner-dot"></span>Harbor Cover</div>
    <span class="slide-arrow prev"><svg width="8" height="10" viewBox="0 0 8 10"><path d="M6 1 L2 5 L6 9" fill="none" stroke="#222" stroke-width="2"/></svg></span>
    <span class="slide-arrow next"><svg width="8" height="10" viewBox="0 0 8 10"><path d="M2 1 L6 5 L2 9" fill="none" stroke="#222" stroke-width="2"/></svg></span>
  </div>
  <p>If you have a network of small businesses, let us help to create additional value for your members and make money for your network. Talk to us today about how we can help.</p>
</article>

<footer class="site-footer">
  <div class="footer-col" style="left:102px">
    <h4>SITE DIRECTORY</h4>
    <ul><li>Search the Directory</li><li>Order a Directory List</li><li>Quote Finder</li><li>Coupon</li><li>Submit Coupon</li><li>Advertise With us</li></ul>
  </div>
  <div class="footer-col" style="left:284px">
    <h4>RESOURCES</h4>
    <ul><li>Join the Forum</li><li>Submit Audio or Video</li><li>Affilates</li><li>Become an Affilate</li><li>Case Studies</li><li>Help Guide</li></ul>
  </div>
  <div class="footer-col" style="left:467px">
    <h4>POPULLAR CATEGORIES</h4>
    <ul><li>Search the Directory</li><li>Order a Directory List</li><li>Quote Finder</li><li>Coupon</li><li>Submit Coupon</li><li>Advertise With us</li></ul>
  </div>
  <div class="footer-col" style="left:678px">
    <h4>ABOUT</h4>
    <ul><li>About Us</li><li>Contact Us</li><li>Terms &amp; Condition</li><li>Privacy</li><li>Support</li><li>Site Map</li></ul>
  </div>
  <div class="footer-col" style="left:808px">
    <h4>FOLLOW US BY</h4>
  </div>
  <span class="social-icon social-a" role="img" aria-label="Social profile link"></span>
  <span class="social-icon social-b" role="img" aria-label="Video channel link"></span>
  <span class="social-icon social-c" role="img" aria-label="Community page link"></span>
  <span class="social-icon social-d" role="img" aria-label="Professional network link"></span>
</footer>

<div class="footer-bar">©2014 tradenestlink. All rights reserved</div>

</body>
</html>
```